Thornbury Building Company - Card Design

I am looking to use the logo designs that you already did for me to develop a business card. I would like the card to have a black background and be double sided. I want white and green logo and text. I have attached an inspiration photo of a look that I like. I would like to use the Vertical Logo attached to take up the full front side of the card. On the back where I have my name and information, I would like to have the horizontal logo or maybe even just the image of the 'A' and trees without the text. I am open, but I am looking for something clean and simple and I want the green to really pop! Additional files can be found under Design #: 58302946

Target Market(s)

Homeowners

Industry/Entity Type

Construction

Contact Information for Business Card

Name: Marcus Thornbury, Title: Project Manager, Phone: 555.274.8136, Email: thornburybuildingcompany@mailvesta.com, address: 487 Larkspur Ln, Ashgrove, NV 95033, Lic# 2468317

Colors
00AB8E
00BBA5
67D7C9
C6EFE9
E9F9F6

Requirements
Nice to have
• I would like to see the logos that I have already got from ArtLoomHub, though I am open to new ones

```html
<!DOCTYPE html>
<html lang="en">
<head>
<meta charset="utf-8">
<title>Thornbury Building Company – Business Cards</title>
<link href="https://fonts.googleapis.com/css2?family=Oswald:wght@300;400;600&display=swap" rel="stylesheet">
<style>
  :root {
    --backdrop: #d6d6d6;
    --card: #1c1c1c;
    --green: #6cc644;
    --white: #ffffff;
    --muted: #e6e6e6;
  }
  html, body {
    margin: 0;
    padding: 0;
    width: 1200px;
    height: 846px;
    overflow: hidden;
    background: var(--backdrop);
  }
  .canvas {
    width: 1200px;
    height: 846px;
    display: flex;
    align-items: center;
    justify-content: center;
    gap: 48px;
  }
  .card {
    width: 520px;
    height: 297px;
    background: var(--card);
    border-radius: 4px;
    box-shadow: 0 14px 30px rgba(0,0,0,0.25);
    position: relative;
    box-sizing: border-box;
    font-family: 'Oswald', sans-serif;
    color: var(--white);
    overflow: hidden;
  }

  /* Back side: contact details */
  .card-back {
    display: flex;
    align-items: center;
    padding: 0 32px;
    gap: 24px;
  }
  .identity {
    width: 200px;
    flex: none;
    display: flex;
    flex-direction: column;
  }
  .brand-mark {
    display: flex;
    align-items: center;
    gap: 8px;
    margin-bottom: 14px;
  }
  .brand-square {
    width: 14px;
    height: 14px;
    background: var(--green);
    flex: none;
  }
  .brand-name {
    font-weight: 400;
    font-size: 15px;
    line-height: 1.15;
    color: var(--white);
    text-transform: uppercase;
    letter-spacing: 0.04em;
  }
  .person-name {
    font-weight: 600;
    font-size: 22px;
    color: var(--green);
    text-transform: uppercase;
    letter-spacing: 0.01em;
    line-height: 1.1;
  }
  .person-title {
    font-weight: 300;
    font-size: 13px;
    color: var(--muted);
    margin-top: 4px;
  }
  .contacts {
    list-style: none;
    margin: 0;
    padding: 0;
    display: flex;
    flex-direction: column;
    gap: 9px;
    min-width: 0;
  }
  .contact-item {
    display: flex;
    align-items: center;
    gap: 8px;
    font-weight: 300;
    font-size: 12px;
    color: var(--muted);
    white-space: nowrap;
  }
  .contact-icon {
    width: 13px;
    height: 13px;
    flex: none;
    fill: var(--green);
  }

  /* Front side: company name */
  .card-front {
    display: flex;
    align-items: center;
    justify-content: center;
  }
  .front-lockup {
    display: flex;
    flex-direction: column;
    align-items: center;
    gap: 14px;
  }
  .front-main {
    display: flex;
    align-items: center;
    gap: 16px;
  }
  .front-square {
    width: 34px;
    height: 34px;
    background: var(--green);
    flex: none;
  }
  .front-name {
    font-weight: 600;
    font-size: 34px;
    line-height: 1.05;
    color: var(--white);
    text-transform: uppercase;
    letter-spacing: 0.05em;
  }
  .established {
    display: flex;
    align-items: center;
    gap: 10px;
    font-weight: 400;
    font-size: 12px;
    letter-spacing: 0.3em;
    color: var(--white);
  }
  .established-rule {
    width: 40px;
    height: 1px;
    background: var(--green);
  }
</style>
</head>
<body>
<main class="canvas">
  <section class="card card-back" aria-label="Business card back">
    <div class="identity">
      <div class="brand-mark">
        <span class="brand-square"></span>
        <span class="brand-name">Thornbury Building Company</span>
      </div>
      <div class="person-name">Marcus Thornbury</div>
      <div class="person-title">Project Manager / Lic# 2468317</div>
    </div>
    <ul class="contacts">
      <li class="contact-item">
        <svg class="contact-icon" viewBox="0 0 24 24" aria-hidden="true"><path d="M6.6 10.8a15.1 15.1 0 0 0 6.6 6.6l2.2-2.2a1 1 0 0 1 1-.25 11.4 11.4 0 0 0 3.6.57 1 1 0 0 1 1 1V20a1 1 0 0 1-1 1A17 17 0 0 1 3 4a1 1 0 0 1 1-1h3.5a1 1 0 0 1 1 1c0 1.25.2 2.45.57 3.57a1 1 0 0 1-.25 1z"/></svg>
        555.274.8136
      </li>
      <li class="contact-item">
        <svg class="contact-icon" viewBox="0 0 24 24" aria-hidden="true"><path d="M2 5h20v14H2z M4 7v.5l8 5 8-5V7l-8 5z" fill-rule="evenodd"/></svg>
        thornburybuildingcompany@mailvesta.com
      </li>
      <li class="contact-item">
        <svg class="contact-icon" viewBox="0 0 24 24" aria-hidden="true"><path d="M12 3 2 12h3v8h5v-5h4v5h5v-8h3z"/></svg>
        487 Larkspur Ln, Ashgrove, NV 95033
      </li>
    </ul>
  </section>

  <section class="card card-front" aria-label="Business card front">
    <div class="front-lockup">
      <div class="front-main">
        <span class="front-square"></span>
        <div class="front-name">Thornbury<br>Building Company</div>
      </div>
      <div class="established">
        <span class="established-rule"></span>
        <span>ESTD 2020</span>
        <span class="established-rule"></span>
      </div>
    </div>
  </section>
</main>
</body>
</html>
```